Puffy Clouds Cotton Candy

Looking for a logo design and business cards to help a 13 year old entrepreneur promote her cotton candy business.
Contact Information for Business Card
Name, Phone & Email
Colors
E54698
E96AAD
F1A4CE
F9D9EA
FCEFF6
A7469A
B969AE
D3A5CF
EDDBEB
F8F0F9
6B429C
8869AF
B7A5CE
E3DAEB
F3F0F8
Requirements
Must have
- A fun feel that is appropriate for a teenage girl selling cotton candy

```html
<!DOCTYPE html>
<html lang="en">
<head>
<meta charset="utf-8">
<title>Puffy Clouds Cotton Candy – Business Card</title>
<link rel="stylesheet" href="https://fonts.googleapis.com/css2?family=Poppins:wght@400;600&family=Arimo:wght@400&display=swap">
<style>
  :root {
    --bg: #1f1f21;
    --card-white: #ffffff;
    --pink: #e54698;
    --purple: #6b429c;
    --magenta: #a7469a;
    --rule: #4a4a4a;
    --white: #ffffff;
  }
  * { margin: 0; padding: 0; box-sizing: border-box; }
  html, body {
    width: 1200px;
    height: 1108px;
    overflow: hidden;
    background: var(--bg);
  }
  .stage {
    position: relative;
    width: 1200px;
    height: 1108px;
  }
  .card {
    position: absolute;
    top: 244px;
    width: 360px;
    height: 620px;
    border-radius: 22px;
    overflow: hidden;
  }
  .card--front {
    left: 200px;
    background: var(--card-white);
    text-align: center;
  }
  .card--back {
    left: 640px;
  }
  .brand-mark {
    display: block;
    margin: 92px auto 0;
  }
  .brand-name {
    margin-top: 26px;
    font-family: "Poppins", sans-serif;
    font-weight: 600;
    font-size: 38px;
    line-height: 1.05;
    color: var(--pink);
    letter-spacing: -0.5px;
  }
  .person {
    margin-top: 104px;
  }
  .person-name {
    font-family: "Poppins", sans-serif;
    font-weight: 600;
    font-size: 27px;
    color: var(--pink);
    line-height: 1.1;
  }
  .person-title {
    font-family: "Arimo", sans-serif;
    font-size: 18px;
    color: var(--purple);
    margin-top: 2px;
  }
  .divider {
    width: 108px;
    height: 1px;
    background: var(--rule);
    margin: 22px auto 16px;
  }
  .contact {
    font-family: "Arimo", sans-serif;
    font-size: 18px;
    color: var(--purple);
    line-height: 1.4;
    list-style: none;
  }
  .back-pattern {
    position: absolute;
    inset: 0;
    background: radial-gradient(circle at 45% 48%, #e54698 0%, #c94aa4 35%, #9a45a0 70%, #7f43a0 100%);
  }
  .back-badge {
    position: absolute;
    right: 46px;
    bottom: 150px;
    display: flex;
    align-items: center;
    gap: 8px;
    font-family: "Poppins", sans-serif;
    font-weight: 600;
    font-size: 14px;
    color: var(--white);
  }
  .back-badge .dot {
    width: 14px;
    height: 14px;
    border: 2px solid var(--white);
    border-radius: 50%;
  }
</style>
</head>
<body>
<main class="stage">
  <section class="card card--front">
    <svg class="brand-mark" width="120" height="120" viewBox="0 0 120 120" aria-hidden="true">
      <circle cx="60" cy="60" r="55" fill="none" stroke="var(--pink)" stroke-width="5"/>
    </svg>
    <h1 class="brand-name">Puffy Clouds<br>Cotton Candy</h1>
    <div class="person">
      <h2 class="person-name">Maya Carter</h2>
      <p class="person-title">Managing Director</p>
    </div>
    <div class="divider"></div>
    <ul class="contact">
      <li>044-987 654 321</li>
      <li>hi@puffyclouds.com</li>
    </ul>
  </section>

  <section class="card card--back">
    <div class="back-pattern" role="img" aria-label="Repeating embossed cotton candy pattern on a pink to purple gradient"></div>
    <div class="back-badge"><span class="dot"></span>Puffy Clouds</div>
  </section>
</main>
</body>
</html>
```